Oriel Photography Business Card

I need a business card designed for a photography business based in Perth, Western Australia called Oriel Photography.

We specialise in wedding, event photography and portrait photography.

The business card must borrow the style of the attached logo.

The hex codes for the colours in the logo are:
#ED1D85 - Pink
#89C23E - Green
#37282F - Black

The name on the card will be:
Name: Tobrian
Phone: 0417395268
Website: www.orielphotography.example.com.au
Facebook: orielphotography

I am open and happy to accept creative concepts.

I’d like some space at the back for writing notes and appointment details.

```html
<!DOCTYPE html>
<html lang="en">
<head>
<meta charset="utf-8">
<title>Oriel Photography Business Card</title>
<link rel="stylesheet" href="https://fonts.googleapis.com/css2?family=Josefin+Sans:wght@400;600&display=swap">
<style>
  :root {
    --pink: #ED1D85;
    --green: #89C23E;
    --ink: #37282F;
    --front-paper: #eef1cf;
    --front-stripe: #e0e6b4;
    --back-paper: #ffffff;
    --back-stripe: #e3e9c2;
    --stage: #f2efe9;
  }
  * { box-sizing: border-box; margin: 0; padding: 0; }
  html, body { width: 1200px; height: 900px; overflow: hidden; }
  body {
    background: var(--stage);
    font-family: "Josefin Sans", sans-serif;
    color: var(--ink);
    position: relative;
  }
  .card {
    position: absolute;
    top: 300px;
    width: 510px;
    height: 290px;
    box-shadow: 0 2px 8px rgba(55, 40, 47, 0.15);
    overflow: hidden;
  }
  .card--front {
    left: 55px;
    background:
      repeating-linear-gradient(90deg, var(--front-stripe) 0 1px, transparent 1px 6px),
      var(--front-paper);
  }
  .card--back {
    left: 635px;
    background:
      linear-gradient(90deg, rgba(255,255,255,0) 0%, #fff 25%, #fff 75%, rgba(255,255,255,0) 100%),
      repeating-linear-gradient(90deg, var(--back-stripe) 0 1px, transparent 1px 6px),
      var(--back-paper);
  }
  .brand-mark {
    position: absolute;
    left: 50%;
    transform: translateX(-50%);
    border-radius: 50%;
    background: var(--pink);
  }
  .card--front .brand-mark { top: 28px; width: 76px; height: 76px; }
  .card--back .brand-mark { top: 38px; width: 46px; height: 46px; }
  .brand-name {
    position: absolute;
    left: 0; right: 0;
    text-align: center;
    text-transform: uppercase;
    color: var(--ink);
    font-weight: 400;
  }
  .card--front .brand-name { top: 128px; font-size: 15px; letter-spacing: 0.42em; }
  .card--back .brand-name { top: 102px; font-size: 9px; letter-spacing: 0.4em; }
  .contact {
    position: absolute;
    top: 178px;
    left: 0; right: 0;
    text-align: center;
    list-style: none;
    text-transform: uppercase;
    font-weight: 600;
    line-height: 20px;
    font-size: 15px;
    letter-spacing: 0.06em;
  }
  .contact__name { color: var(--pink); font-size: 16px; }
  .contact__web { font-size: 13px; }
  .contact__web-prefix { color: var(--green); }
  .contact__icon {
    display: inline-block;
    width: 14px; height: 14px;
    border-radius: 3px;
    background: var(--green);
    vertical-align: -1px;
    margin-right: 6px;
  }
  .contact__icon svg { display: block; }
  .notes-icon {
    position: absolute;
    top: 124px;
    left: 128px;
    width: 16px; height: 16px;
    border-radius: 3px;
    background: var(--green);
  }
</style>
</head>
<body>
  <section class="card card--front" aria-label="Business card front">
    <div class="brand-mark" aria-hidden="true"></div>
    <h1 class="brand-name">Oriel Photography</h1>
    <ul class="contact">
      <li class="contact__name">Tobrian</li>
      <li class="contact__phone">
        <span class="contact__icon">
          <svg width="14" height="14" viewBox="0 0 14 14" aria-hidden="true">
            <path d="M4 3 L5.5 3 L6 5 L5 6 Q6 8 8 9 L9 8 L11 8.5 L11 10 Q10 11 8.5 11 Q3 9.5 3 4.5 Q3 3.5 4 3Z" fill="#fff"/>
          </svg>
        </span>0417395268
      </li>
      <li class="contact__web"><span class="contact__web-prefix">www.</span>orielphotography.example.com.au</li>
      <li class="contact__social"><span class="contact__icon"></span>orielphotography</li>
    </ul>
  </section>

  <section class="card card--back" aria-label="Business card back with space for notes">
    <div class="brand-mark" aria-hidden="true"></div>
    <h2 class="brand-name">Oriel Photography</h2>
    <span class="notes-icon">
      <svg width="16" height="16" viewBox="0 0 16 16" aria-hidden="true">
        <path d="M4 12 L5 9 L10.5 3.5 L12.5 5.5 L7 11 Z" fill="none" stroke="#fff" stroke-width="1.2" stroke-linejoin="round"/>
      </svg>
    </span>
  </section>
</body>
</html>
```